4th Generation Family Business Needs a New Card Design!

We are a family owned 4th Generation company. We are based in the Sydney, Australia area and we are desperately in need of a more modern and classy card. We are monumental masons who design, supply & erect lasting memorials throughout cemeteries in Sydney. Our customers are normally in a period of grieving. I have attached logo files that will need to be implemented on the card. Company was established 1935. Australian Owned and Operated. Card needs to be designed to PIXO.com specification.

Target Market(s)

Our target market is based upon people that a grieving for family members that have passed away. We also deal with alot of companies that own and operate cemeteries.

Industry/Entity Type

Business

Contact Information for Business Card

Simon Harcourt, Operations Manager, 0417293086, simon@harcourtmemorials.com.au
Lewis Harcourt, Director, 0491630572, lewis@harcourtmemorials.com.au
Phone # 02 9561 3048
Website: www.harcourtmemorials.com.au
Address: Suite 17, 8 Palfrey Lane, West Carlow, Sydney NSW 2156

Font styles to use
Serif
Decorative
Script

Requirements
Must have
• Would like to see the logo nicely implemented with a modern design. Embossed lettering would be a nice additive.

```html
<!DOCTYPE html>
<html lang="en">
<head>
<meta charset="utf-8">
<title>Harcourt Memorials – Business Card</title>
<link rel="stylesheet" href="https://fonts.googleapis.com/css2?family=Cinzel:wght@400;600&family=PT+Serif:ital@0;1&display=swap">
<style>
  :root {
    --backdrop: #e6e6e6;
    --card-black: #0b0b0c;
    --card-sheen: #2a2b2d;
    --gold: #e0b52a;
    --gold-deep: #c99a12;
    --white: #ffffff;
    --ink: #111111;
    --serif-display: "Cinzel", "Times New Roman", serif;
    --serif-text: "PT Serif", Georgia, serif;
  }
  * { box-sizing: border-box; margin: 0; padding: 0; }
  html, body { width: 1200px; height: 576px; overflow: hidden; }
  body { background: var(--backdrop); position: relative; }

  .card {
    position: absolute;
    top: 138px;
    width: 484px;
    height: 293px;
    overflow: hidden;
    background:
      linear-gradient(100deg, transparent 22%, rgba(255,255,255,0.10) 30%, transparent 40%),
      radial-gradient(ellipse at 40% 45%, var(--card-sheen) 0%, var(--card-black) 70%);
    box-shadow: 0 2px 5px rgba(0,0,0,0.35);
  }
  .card--front { left: 81px; }
  .card--back { left: 602px; width: 482px; }

  .front-band {
    position: absolute;
    left: 0; right: 0; bottom: 0;
    height: 11px;
    background: linear-gradient(90deg, var(--gold-deep), var(--gold));
  }

  .wordmark {
    position: absolute;
    text-align: center;
    color: var(--white);
    font-family: var(--serif-display);
    font-weight: 400;
    line-height: 1;
  }
  .wordmark__name { display: block; font-size: 38px; letter-spacing: 1px; }
  .wordmark__sub { display: block; font-size: 17px; letter-spacing: 3px; margin-top: 8px; }
  .card--front .wordmark { left: 0; right: 0; top: 112px; }
  .card--back .wordmark { left: 14px; width: 220px; top: 140px; }
  .card--back .wordmark__name { font-size: 33px; }
  .card--back .wordmark__sub { font-size: 15px; }

  .swoosh { position: absolute; left: 0; bottom: 0; width: 482px; height: 292px; }

  .person {
    position: absolute;
    right: 22px;
    top: 30px;
    text-align: right;
    color: var(--white);
  }
  .person__name { font-family: var(--serif-display); font-size: 21px; font-weight: 400; letter-spacing: 1px; line-height: 1; }
  .person__role { font-family: var(--serif-text); font-style: italic; font-size: 12px; margin-top: 3px; }

  .address {
    position: absolute;
    right: 22px;
    top: 85px;
    text-align: right;
    color: var(--white);
    font-family: var(--serif-text);
    font-size: 12.5px;
    line-height: 17px;
    font-style: normal;
  }

  .contacts {
    position: absolute;
    right: 20px;
    top: 206px;
    list-style: none;
    color: var(--ink);
    font-family: var(--serif-text);
    font-size: 12.5px;
    line-height: 16.7px;
    text-align: right;
  }
  .contacts li { display: flex; justify-content: flex-end; align-items: center; gap: 5px; }
  .contacts svg { width: 9px; height: 9px; fill: var(--ink); flex: none; }
</style>
</head>
<body>

  <section class="card card--front" aria-label="Card front">
    <div class="wordmark">
      <span class="wordmark__name">HARCOURT</span>
      <span class="wordmark__sub">MEMORIALS</span>
    </div>
    <div class="front-band"></div>
  </section>

  <section class="card card--back" aria-label="Card back">
    <svg class="swoosh" viewBox="0 0 602 365" preserveAspectRatio="none" aria-hidden="true">
      <defs>
        <linearGradient id="goldFill" x1="0" y1="0" x2="1" y2="1">
          <stop offset="0" stop-color="#c99a12"/>
          <stop offset="0.5" stop-color="#e6bd32"/>
          <stop offset="1" stop-color="#d6a81c"/>
        </linearGradient>
      </defs>
      <path d="M0,365 L0,338 C120,348 260,330 360,292 C440,262 520,215 602,206 L602,365 Z" fill="url(#goldFill)"/>
      <path d="M0,326 C120,336 255,318 352,282 C432,252 515,206 602,196 L602,206 C520,215 440,262 360,292 C260,330 120,348 0,338 Z" fill="#0b0b0c"/>
      <path d="M30,300 C150,320 260,306 345,270 C428,236 510,190 602,178 L602,195 C512,206 432,250 350,280 C262,314 150,324 30,300 Z" fill="#ffffff"/>
      <path d="M45,312 C160,330 250,318 320,300 C255,324 160,336 45,312 Z" fill="#ffffff"/>
    </svg>

    <div class="wordmark">
      <span class="wordmark__name">HARCOURT</span>
      <span class="wordmark__sub">MEMORIALS</span>
    </div>

    <div class="person">
      <h1 class="person__name">SIMON HARCOURT</h1>
      <p class="person__role">Operations Manager</p>
    </div>

    <address class="address">
      Suite 17, 8 Palfrey Lane,<br>
      West Carlow, Sydney NSW 2156
    </address>

    <ul class="contacts">
      <li>0491630572
        <svg viewBox="0 0 10 10"><path d="M2 0.5 L3.6 2.6 L2.8 3.6 C3.4 4.9 4.6 6.1 6 6.8 L7 6 L9.5 7.6 L8.6 9.5 C4.5 9.2 0.8 5.5 0.5 1.4 Z"/></svg>
      </li>
      <li>02 9561 3048
        <svg viewBox="0 0 10 10"><path d="M1 3 C1 1.5 9 1.5 9 3 L9 4 L7 4 L7 3 L3 3 L3 4 L1 4 Z M2 5 L8 5 L9 9 L1 9 Z"/></svg>
      </li>
      <li>harcourtmemorials.com.au
        <svg viewBox="0 0 10 10"><path d="M0.5 2 L9.5 2 L9.5 8 L0.5 8 Z M1 2.5 L5 5.5 L9 2.5 L9 3.2 L5 6.2 L1 3.2 Z" fill-rule="evenodd"/></svg>
      </li>
      <li>lewis@harcourtmemorials.com.au
        <svg viewBox="0 0 10 10"><circle cx="5" cy="5" r="4.5"/><path d="M0.5 5 L9.5 5 M5 0.5 L5 9.5" stroke="#e0b52a" stroke-width="0.8"/></svg>
      </li>
    </ul>
  </section>

</body>
</html>
```